Nutrition business needs logo & business card design

We need a business card & logo design for a new company based in Toronto, Ontario Canada called Verdel Wellworks.

We provide nutrition service using metrics as guide to manage client's progress. Our service creates individualized nutrition and lifestyle strategies that focuses on improving Performance, Longevity and Weight Loss. I would like to see designs that use the color of green, gray, blue and white.

The final design should:

--convey a feeling of connectedness with positive transformation.

-- communicate the idea of awareness with guided effort that yields personal independence for a better and more productive life

Target Market(s)

Professionals who work in the IT/Computer/Engineering/Banking industry specifically Directors, Managers, CEO's.

Industry/Entity Type

Health And Wellness

Contact Information for Business Card

Dorvane Pike, Owner
email: DPIKE@verdelwellworks.example
tel: - 555-204-7718

Logo Text

better health through analytics or measure to manage

Font styles to use
Other font styles liked:
• Garamound

Colors
ffffff
abd037
85acd3
757575
34a7d7

Requirements
Must have
• Good contrast and decent size font - ease of readability, aesthetically nice colors
Nice to have
• image of chart or graph that conveys measurement or analytics
Should not have
• Borders, images of food,

```html
<!DOCTYPE html>
<html lang="en">
<head>
<meta charset="utf-8">
<title>Verdel Wellworks – Business Card</title>
<link rel="stylesheet" href="https://fonts.googleapis.com/css2?family=Questrial&family=Source+Sans+3:wght@400;600&display=swap">
<style>
  :root {
    --stage: #3a3532;
    --card: #111111;
    --card-edge: #1c1c1c;
    --green: #8cc63f;
    --text-light: #f2f2f2;
    --brand-gray: #5e5e5e;
  }
  * { box-sizing: border-box; margin: 0; padding: 0; }
  html, body { width: 1200px; height: 900px; overflow: hidden; }
  body {
    background: var(--stage);
    font-family: "Source Sans 3", "Helvetica Neue", Arial, sans-serif;
    position: relative;
  }
  .card {
    position: absolute;
    top: 305px;
    width: 500px;
    height: 290px;
    background: var(--card);
    border: 1px solid var(--card-edge);
    box-shadow: 0 10px 30px rgba(0,0,0,.45);
  }
  .card--front { left: 70px; }
  .card--back  { left: 630px; }

  /* Front */
  .brand-mark {
    position: absolute;
    left: 40px; top: 60px;
    width: 170px;
    text-align: center;
  }
  .brand-mark__circle {
    width: 130px; height: 130px;
    border-radius: 50%;
    background: var(--green);
    margin: 0 auto 14px;
  }
  .brand-mark__name {
    font-weight: 600;
    font-size: 17px;
    color: var(--green);
  }
  .divider {
    position: absolute;
    left: 232px; top: 48px;
    width: 1px; height: 196px;
    background: linear-gradient(to bottom, rgba(140,198,63,0), var(--green) 30%, var(--green) 70%, rgba(140,198,63,0));
  }
  .contact {
    position: absolute;
    left: 250px; top: 50px;
    color: var(--text-light);
    font-size: 15px;
    line-height: 1.25;
  }
  .contact__name { color: var(--green); font-weight: 600; font-size: 17px; }
  .contact__role { margin-bottom: 16px; }
  .contact__address { margin-bottom: 16px; }
  .contact__line { display: flex; align-items: center; gap: 8px; }
  .contact__line svg { width: 11px; height: 11px; flex: none; }

  /* Back */
  .back-brand {
    position: absolute;
    inset: 0;
    display: flex;
    flex-direction: column;
    align-items: center;
    justify-content: center;
    gap: 14px;
  }
  .back-brand__circle {
    width: 58px; height: 58px;
    border-radius: 50%;
    background: var(--green);
  }
  .back-brand__name {
    font-family: "Questrial", "Century Gothic", sans-serif;
    font-size: 40px;
    color: var(--brand-gray);
    letter-spacing: .5px;
  }
</style>
</head>
<body>

<section class="card card--front" aria-label="Business card front">
  <div class="brand-mark">
    <div class="brand-mark__circle"></div>
    <div class="brand-mark__name">Verdel Wellworks</div>
  </div>
  <div class="divider"></div>
  <div class="contact">
    <div class="contact__name">Dorvane Pike</div>
    <div class="contact__role">Owner</div>
    <div class="contact__address">Toronto, Ontario<br>Canada</div>
    <div class="contact__line">
      <svg viewBox="0 0 12 12" aria-hidden="true"><path fill="#8cc63f" d="M2.5 0.8 4.4 3 3.4 4.3c.7 1.6 2.3 3.2 3.9 3.9l1.3-1 2.2 1.9-.9 2C5.7 10.9 1.1 6.3.5 1.7z"/></svg>
      <span>555-204-7718</span>
    </div>
    <div class="contact__line">
      <svg viewBox="0 0 12 12" aria-hidden="true"><rect x="0.5" y="2" width="11" height="8" fill="#8cc63f"/><path d="M0.8 2.4 6 6.6l5.2-4.2" fill="none" stroke="#111" stroke-width="1"/></svg>
      <span>DPIKE@verdelwellworks.example</span>
    </div>
    <div class="contact__line">
      <svg viewBox="0 0 12 12" aria-hidden="true"><circle cx="6" cy="6" r="5.5" fill="#8cc63f"/><path d="M.8 6h10.4M6 .6c-2.4 2.8-2.4 8 0 10.8M6 .6c2.4 2.8 2.4 8 0 10.8" fill="none" stroke="#111" stroke-width=".9"/></svg>
      <span>www.verdelwellworks.example</span>
    </div>
  </div>
</section>

<section class="card card--back" aria-label="Business card back">
  <div class="back-brand">
    <div class="back-brand__circle"></div>
    <div class="back-brand__name">Verdel Wellworks</div>
  </div>
</section>

</body>
</html>
```